The Harbourlight Aid Trust needs a graphic of their innovation approach

What we need?
- we have designed a new innovation approach (see attached). An innovation approach is the process one goes through in order to design and launch a new product or service.
- This new graphic will be used in meetings to help others understand what innovation is and how we do it. It will also be used in training sessions and be the starting point for innovation training materials we are creating
- We have created this draft graphic by copying and pasting new words over another charities innovation process
- We would like you to use your design magic and create our very own innovation process graphic. We would like it to be neat, simple, non fussy, easy to understand /read and in line with our brand colours
Attached:
1. PowerPoint:
- Slide 1: our innovation process
- Slide 2 explanation of process to bring it to life
- Slide 3&4: brand colours
- Slide 5: inspiration / examples of other processes we like the look of
2. Typeface brand guidelines
We can't wait to see what you come up with! Thank you :)
Target Market(s)
internal employees
Industry/Entity Type
Charity
Colors
Designer to choose colors to be used in the design.
Look and feel
Each slider illustrates characteristics of the customer's brand and the style your logo design should communicate.

```html
<!DOCTYPE html>
<html lang="en">
<head>
<meta charset="utf-8">
<title>Harbourlight Aid Trust – Innovation Approach</title>
<link rel="stylesheet" href="https://fonts.googleapis.com/css2?family=Arimo:wght@400;700&display=swap">
<style>
  :root {
    --discover: #e31e24;
    --discover-soft: #f29090;
    --define: #f4b03f;
    --define-soft: #f9d9a0;
    --deliver: #1a8bbf;
    --deliver-soft: #8cc7e0;
    --ink: #111111;
    --paper: #ffffff;
  }
  html, body {
    margin: 0;
    padding: 0;
    width: 1200px;
    height: 809px;
    overflow: hidden;
    background: var(--paper);
  }
  .process-map {
    display: block;
    width: 1200px;
    height: 809px;
    font-family: "Arimo", Arial, sans-serif;
  }
  .phase-title { font-size: 21px; font-weight: 700; text-anchor: middle; }
  .step-label { font-size: 14px; fill: var(--ink); text-anchor: middle; }
  .link-label { font-size: 15.5px; text-anchor: middle; }
  .discover { fill: var(--discover); }
  .discover-soft { fill: var(--discover-soft); }
  .define { fill: var(--define); }
  .define-soft { fill: var(--define-soft); }
  .deliver { fill: var(--deliver); }
  .deliver-soft { fill: var(--deliver-soft); }
  .ring { fill: var(--paper); stroke-width: 9; }
  .flow { fill: none; stroke-width: 7; }
  .loop { fill: none; stroke-width: 4.5; stroke-dasharray: 11 6; }
</style>
</head>
<body>
<svg class="process-map" viewBox="0 0 850 573" xmlns="http://www.w3.org/2000/svg" role="img" aria-label="Innovation approach: Discover, Define, Deliver">

  <!-- Phase titles -->
  <text class="phase-title discover" x="125" y="73">Discover</text>
  <text class="phase-title define" x="452" y="73">Define</text>
  <text class="phase-title deliver" x="722" y="73">Deliver</text>

  <!-- Discover: Challenge → Opportunity -->
  <path class="flow" stroke="var(--discover)" d="M97 242 V172 Q97 147 122 147 H196"/>
  <polygon class="discover" points="205,147 193,139 193,155"/>
  <path class="loop" stroke="var(--discover-soft)" d="M198 160 H132 Q110 160 110 182 V236"/>
  <polygon class="discover-soft" points="110,244 104,234 116,234"/>
  <text class="link-label discover" x="145" y="129">Insight</text>
  <text class="link-label discover-soft" x="155" y="188">Interate</text>

  <!-- Opportunity → Concepts -->
  <path class="flow" stroke="var(--discover)" d="M316 148 H398 Q412 148 419 156"/>
  <path class="flow" stroke="var(--define)" d="M419 156 Q425 164 425 176 V244"/>
  <polygon class="define" points="425,253 417,241 433,241"/>
  <path class="loop" stroke="var(--define-soft)" d="M411 240 V185"/>
  <path class="loop" stroke="var(--discover-soft)" d="M411 185 Q411 160 388 160 H330"/>
  <polygon class="discover-soft" points="321,160 331,154 331,166"/>
  <text class="link-label discover" x="363" y="131">Ideate</text>
  <text class="link-label discover-soft" x="363" y="188">Interate</text>
  <text class="link-label define" x="480" y="208">(In)validate</text>

  <!-- Concepts → Solution -->
  <path class="flow" stroke="var(--define)" d="M424 366 V446 Q424 468 446 468 H520"/>
  <polygon class="define" points="530,468 518,460 518,476"/>
  <path class="loop" stroke="var(--define-soft)" d="M520 483 H432 Q410 483 410 461 V382"/>
  <polygon class="define-soft" points="410,373 404,383 416,383"/>
  <text class="link-label define" x="478" y="452">Test</text>
  <text class="link-label define-soft" x="474" y="502">Interate</text>

  <!-- Solution → Launch -->
  <path class="flow" stroke="var(--deliver)" d="M636 467 H722 Q745 467 745 444 V376"/>
  <polygon class="deliver" points="745,366 737,378 753,378"/>
  <path class="loop" stroke="var(--deliver-soft)" d="M759 378 V458 Q759 481 736 481 H664"/>
  <polygon class="deliver-soft" points="655,481 665,475 665,487"/>
  <text class="link-label deliver" x="690" y="434">Delivery</text>
  <text class="link-label deliver" x="690" y="456">Plan</text>
  <text class="link-label deliver-soft" x="720" y="500">Continuous</text>
  <text class="link-label deliver-soft" x="720" y="522">Improvement</text>

  <!-- Launch upward -->
  <path class="flow" stroke="var(--deliver)" d="M745 252 V184"/>
  <polygon class="deliver" points="745,170 735,186 755,186"/>

  <!-- Step: Challenge -->
  <g class="step step-challenge">
    <circle class="ring" stroke="var(--discover)" cx="97" cy="296" r="55"/>
    <g fill="none" stroke="var(--discover)" stroke-width="3">
      <circle cx="95" cy="298" r="19"/>
      <circle cx="95" cy="298" r="11"/>
      <circle cx="95" cy="298" r="3.5" fill="var(--discover)"/>
      <path d="M95 298 L117 276"/>
    </g>
    <polygon class="discover" points="113,272 122,270 126,274 118,282"/>
    <text class="step-label" x="97" y="340">Challenge</text>
  </g>

  <!-- Step: Opportunity Statement -->
  <g class="step step-opportunity">
    <circle class="ring" stroke="var(--discover)" cx="260" cy="148" r="57"/>
    <g fill="none" stroke="var(--discover)" stroke-width="3.5" stroke-linecap="round">
      <path d="M257 142 V124"/>
      <path d="M257 127 Q257 118 245 111"/>
      <path d="M257 127 Q257 118 269 111"/>
      <path d="M257 124 V107"/>
    </g>
    <polygon class="discover" points="257,100 251,109 263,109"/>
    <polygon class="discover" points="240,107 241,116 248,111"/>
    <polygon class="discover" points="274,107 273,116 266,111"/>
    <text class="step-label" x="260" y="166">Opportunity</text>
    <text class="step-label" x="260" y="184">Statement</text>
  </g>

  <!-- Step: Concepts -->
  <g class="step step-concepts">
    <circle class="ring" stroke="var(--define)" cx="424" cy="310" r="57"/>
    <g fill="none" stroke="var(--define)" stroke-width="2.5" stroke-linecap="round">
      <path d="M413 311 Q405 303 405 293 A18 18 0 0 1 441 293 Q441 303 433 311 V318 H413 Z"/>
      <path d="M415 322 H431"/>
      <path d="M418 326 H428"/>
      <path d="M423 267 V272 M398 277 L402 281 M448 277 L444 281 M390 293 H395 M451 293 H456"/>
      <circle cx="420" cy="292" r="5"/>
      <circle cx="429" cy="302" r="3.5"/>
    </g>
    <text class="step-label" x="424" y="342">Concepts</text>
  </g>

  <!-- Step: Solution -->
  <g class="step step-solution">
    <circle class="ring" stroke="var(--deliver)" cx="580" cy="467" r="55"/>
    <g class="deliver">
      <rect x="561" y="438" width="19" height="19"/>
      <rect x="582" y="438" width="19" height="19"/>
      <rect x="561" y="459" width="19" height="19"/>
      <rect x="588" y="467" width="20" height="20"/>
      <circle cx="580" cy="447" r="4"/>
      <circle cx="570" cy="457" r="4"/>
    </g>
    <text class="step-label" x="578" y="511">Solution</text>
  </g>

  <!-- Step: Launch -->
  <g class="step step-launch">
    <circle class="ring" stroke="var(--deliver)" cx="745" cy="310" r="55"/>
    <path class="deliver" d="M745 266 Q755 278 755 298 V314 H735 V298 Q735 278 745 266 Z"/>
    <polygon class="deliver" points="735,302 727,318 735,314"/>
    <polygon class="deliver" points="755,302 763,318 755,314"/>
    <circle cx="745" cy="288" r="3.5" fill="var(--paper)"/>
    <g stroke="var(--deliver)" stroke-width="1.5">
      <path d="M740 318 V328 M745 318 V330 M750 318 V328"/>
    </g>
    <text class="step-label" x="745" y="350">Launch</text>
  </g>
</svg>
</body>
</html>
```